Corvel Capital LLC

Need Professional Business cards for New Investment Fund

Target Market(s)

High Quality investors

Industry/Entity Type

Financial

Contact Information for Business Card

Phone Number +1 555 284 6190
Name Lukas Varenko
Title Fund Manager
email lv@FundCorvel.com
Website www.FundCorvel.com

Colors

Designer to choose colors to be used in the design.

Requirements
Must have
• Must have our Logo and all of the above. Must be made so lettering and loge can be raised

```html
<!DOCTYPE html>
<html lang="en">
<head>
<meta charset="UTF-8">
<title>Halvenor – Business Cards</title>
<link href="https://fonts.googleapis.com/css2?family=Poppins:wght@400;600&display=swap" rel="stylesheet">
<style>
  :root {
    --backdrop: #d9d9d9;
    --paper: #ffffff;
    --forest: #3e4a3f;
    --forest-light: #4a574b;
    --lime: #22ee00;
    --ink-grey: #4d4d4d;
    --white: #ffffff;
  }
  * { box-sizing: border-box; margin: 0; padding: 0; }
  html, body {
    width: 1200px; height: 801px; overflow: hidden;
    background: var(--backdrop);
    font-family: "Poppins", sans-serif;
  }
  .stage {
    position: relative; width: 1200px; height: 801px;
    display: flex; align-items: center; justify-content: center; gap: 44px;
  }
  .card {
    position: relative; width: 540px; height: 310px;
    border-bottom: 3px solid var(--lime);
    border-left: 3px solid var(--lime);
    box-shadow: 0 10px 24px rgba(0,0,0,0.18);
  }
  /* front */
  .card-front { background: var(--paper); }
  .holder { position: absolute; top: 28px; right: 34px; text-align: right; }
  .holder-name { color: var(--lime); font-weight: 600; font-size: 22px; line-height: 1.1; }
  .holder-title { color: var(--ink-grey); font-size: 13px; margin-top: 2px; }
  .front-brand {
    position: absolute; left: 0; right: 0; top: 122px; text-align: center;
    color: var(--forest); font-weight: 600; font-size: 38px; letter-spacing: 1px;
  }
  .contact { position: absolute; left: 30px; bottom: 24px; list-style: none; }
  .contact li {
    display: flex; align-items: center; gap: 10px;
    color: var(--ink-grey); font-size: 13px; line-height: 21px;
  }
  .contact svg { width: 12px; height: 12px; flex: none; }
  /* back */
  .card-back {
    background: linear-gradient(160deg, var(--forest) 0%, var(--forest-light) 100%);
  }
  .back-brand {
    position: absolute; left: 0; right: 0; top: 104px; text-align: center;
    color: var(--white); font-weight: 600; font-size: 40px; letter-spacing: 2px;
  }
  .back-web {
    position: absolute; left: 0; right: 0; bottom: 40px; text-align: center;
    color: var(--white); font-size: 14px; letter-spacing: 4px;
  }
</style>
</head>
<body>
<main class="stage">
  <section class="card card-front">
    <div class="holder">
      <p class="holder-name">Lukas Varenko</p>
      <p class="holder-title">Fund Manager</p>
    </div>
    <p class="front-brand">Halvenor</p>
    <ul class="contact">
      <li>
        <svg viewBox="0 0 12 12" aria-hidden="true"><path d="M2.5 1 L4.5 1 L5 3.5 L3.8 4.6 Q5 7 7.4 8.2 L8.5 7 L11 7.5 L11 9.5 Q10.5 11 9 11 Q1 10 1 3 Q1 1.5 2.5 1 Z" fill="var(--lime)"/></svg>
        +1 555 284 6190
      </li>
      <li>
        <svg viewBox="0 0 12 12" aria-hidden="true"><rect x="0.5" y="2" width="11" height="8" rx="1" fill="var(--lime)"/><path d="M1 2.5 L6 6.5 L11 2.5" stroke="#fff" stroke-width="1" fill="none"/></svg>
        lv@FundCorvel.com
      </li>
      <li>
        <svg viewBox="0 0 12 12" aria-hidden="true"><circle cx="6" cy="6" r="5.5" fill="var(--lime)"/><path d="M0.5 6 H11.5 M6 0.5 Q3 6 6 11.5 M6 0.5 Q9 6 6 11.5" stroke="#fff" stroke-width="0.8" fill="none"/></svg>
        www.FundCorvel.com
      </li>
    </ul>
  </section>

  <section class="card card-back">
    <p class="back-brand">Halvenor</p>
    <p class="back-web">www.FundCorvel.com</p>
  </section>
</main>
</body>
</html>
```